Business Card Design - Amberfield Court

We are looking at a new design for our business cards that has a modern and professional look. We run a residential aged care facility focussing on the care of residents. The cards will be used for potential clients, consultants and business opportunities in this sector. Blue and white is our main colours and would to see these colours incorporated in the design.
Industry/Entity Type
Business
Contact Information for Business Card
Amberfield Court, Darren Walsh, dwalsh@amberfieldcourt.com.au, Finance Manager, 0472 639 208, BCom, 37 Marrabel Crescent, Brindle Vale, Qld 4093.
Look and feel
Each slider illustrates characteristics of the customer's brand and the style your logo design should communicate.

```html
<!DOCTYPE html>
<html lang="en">
<head>
<meta charset="utf-8">
<title>Amberfield Court – Business Card</title>
<link rel="stylesheet" href="https://fonts.googleapis.com/css2?family=PT+Sans+Narrow:wght@400;700&family=Open+Sans:ital,wght@0,400;0,600;1,400&display=swap">
<style>
  :root {
    --page: #ecebe8;
    --white: #ffffff;
    --blue-deep: #3f7d94;
    --blue-mid: #5a9ab0;
    --blue-light: #8cc0d0;
    --ink-blue: #3a6678;
    --ink-light: #e8f3f7;
    --band-grey: #c8c2bc;
    --tag-grey: #8f8a85;
  }
  * { margin: 0; padding: 0; box-sizing: border-box; }
  html, body { width: 1200px; height: 1023px; overflow: hidden; background: var(--page); }
  .sheet { position: relative; width: 1200px; height: 1023px; }
  .card {
    position: absolute; left: 180px; width: 840px; height: 480px;
    overflow: hidden; box-shadow: 0 4px 14px rgba(0,0,0,0.15);
  }
  .card--front { top: 20px; background: var(--white); }
  .card--back { top: 523px; background: linear-gradient(135deg, var(--blue-deep) 0%, var(--blue-mid) 55%, var(--blue-light) 100%); }
  .card__art { position: absolute; inset: 0; width: 100%; height: 100%; }

  .brand { position: absolute; left: 48px; top: 52px; display: flex; align-items: center; gap: 16px; }
  .brand__dot { width: 60px; height: 60px; border-radius: 50%; background: var(--blue-mid); flex: none; }
  .brand__text { display: flex; flex-direction: column; align-items: flex-start; gap: 6px; }
  .brand__name {
    font-family: "PT Sans Narrow", sans-serif; font-weight: 400;
    font-size: 34px; line-height: 1; letter-spacing: 3px; color: var(--blue-mid); text-transform: uppercase;
  }
  .brand__tagline {
    font-family: "Open Sans", sans-serif; font-size: 13px; line-height: 1;
    color: var(--white); background: var(--band-grey); padding: 4px 8px;
  }

  .person { position: absolute; left: 48px; top: 378px; font-family: "PT Sans Narrow", sans-serif; }
  .person__name { font-size: 38px; line-height: 1.1; font-weight: 700; letter-spacing: 1px; color: var(--ink-blue); text-transform: uppercase; }
  .person__role { font-size: 17px; letter-spacing: 1px; color: var(--ink-light); text-transform: uppercase; }

  .contact { position: absolute; left: 470px; top: 214px; list-style: none;
    font-family: "Open Sans", sans-serif; font-size: 17px; line-height: 31px; color: var(--ink-light); }
  .contact__item { display: flex; align-items: center; gap: 10px; }
  .contact__item--plain { padding-left: 28px; text-transform: uppercase; font-family: "PT Sans Narrow", sans-serif; font-size: 19px; letter-spacing: 1px; }
  .contact__icon { width: 18px; height: 18px; flex: none; }

  .back-title { position: absolute; left: 56px; top: 56px; }
  .back-title__name {
    font-family: "PT Sans Narrow", sans-serif; font-size: 48px; letter-spacing: 6px;
    color: var(--ink-blue); text-transform: uppercase;
  }
  .back-title__tagline {
    font-family: "Open Sans", sans-serif; font-style: italic; font-size: 24px; color: var(--ink-light); margin-top: 6px;
  }
  .back-motif {
    position: absolute; left: 330px; top: 250px; width: 540px; height: 260px;
    border-radius: 50% 50% 0 0;
    background: radial-gradient(ellipse at 60% 60%, rgba(58,102,120,0.45), rgba(58,102,120,0.1) 70%, rgba(58,102,120,0) 100%);
  }
</style>
</head>
<body>
<main class="sheet">

  <section class="card card--front" aria-label="Business card front">
    <svg class="card__art" viewBox="0 0 840 480" preserveAspectRatio="none" aria-hidden="true">
      <defs>
        <linearGradient id="front-blue" x1="0" y1="1" x2="1" y2="0">
          <stop offset="0" stop-color="#4f8ea5"/>
          <stop offset="0.6" stop-color="#6eaabd"/>
          <stop offset="1" stop-color="#8cc0d0"/>
        </linearGradient>
      </defs>
      <path d="M0 318 C 200 306, 360 240, 450 120 C 500 50, 545 -2, 600 -2" fill="none" stroke="#c8c2bc" stroke-width="14"/>
      <path d="M0 340 C 210 330, 380 260, 470 135 C 520 62, 565 0, 620 0 L840 0 L840 480 L0 480 Z" fill="url(#front-blue)"/>
    </svg>

    <div class="brand">
      <span class="brand__dot" aria-hidden="true"></span>
      <div class="brand__text">
        <span class="brand__name">Amberfield Court</span>
        <span class="brand__tagline">Comfort, Respect, Belonging</span>
      </div>
    </div>

    <div class="person">
      <p class="person__name">Darren Walsh</p>
      <p class="person__role">Finance Manager</p>
    </div>

    <ul class="contact">
      <li class="contact__item">
        <svg class="contact__icon" viewBox="0 0 18 18" aria-hidden="true"><rect x="1" y="1" width="16" height="16" rx="2" fill="#3a6678"/><path d="M5 4h3l1 3-2 1a7 7 0 0 0 3 3l1-2 3 1v3c-5 0-9-4-9-9z" fill="#e8f3f7"/></svg>
        0472 639 208
      </li>
      <li class="contact__item">
        <svg class="contact__icon" viewBox="0 0 18 18" aria-hidden="true"><rect x="1" y="1" width="16" height="16" rx="2" fill="#3a6678"/><rect x="4" y="5.5" width="10" height="7" fill="none" stroke="#e8f3f7" stroke-width="1.2"/><path d="M4 5.5l5 4 5-4" fill="none" stroke="#e8f3f7" stroke-width="1.2"/></svg>
        dwalsh@amberfieldcourt.com.au
      </li>
      <li class="contact__item contact__item--plain">BCom, 37 Marrabel Crescent</li>
      <li class="contact__item contact__item--plain">Brindle Vale, Qld 4093.</li>
    </ul>
  </section>

  <section class="card card--back" aria-label="Business card back">
    <div class="back-title">
      <p class="back-title__name">Amberfield Court</p>
      <p class="back-title__tagline">Comfort, Respect, Belonging</p>
    </div>
    <div class="back-motif" role="img" aria-label="Faint large brand emblem area"></div>
  </section>

</main>
</body>
</html>
```